Copper Lantern

Need a business card for our restaurant. Restaurant and Bar in the mountains of North Idaho. Rustic looking card

rustic design, wood and metal looking, primarily neutral colors

• Name, address, phone number, website, email address

```html
<!DOCTYPE html>
<html lang="en">
<head>
<meta charset="utf-8">
<title>Copper Lantern – Business Card</title>
<link rel="stylesheet" href="https://fonts.googleapis.com/css2?family=Lato:wght@400;700&display=swap">
<style>
  :root {
    --backdrop: #6a6a6a;
    --card-dark: #1d1d1d;
    --card-face: #232323;
    --pattern-light: #3a3a3a;
    --pattern-deep: #121212;
    --ink: #f2f2f2;
    --ink-soft: #d6d6d6;
    --rule: #cfcfcf;
    --badge: #ffffff;
    --badge-ink: #1d1d1d;
  }
  * { box-sizing: border-box; margin: 0; padding: 0; }
  html, body { width: 1200px; height: 900px; overflow: hidden; }
  body {
    background: var(--backdrop);
    font-family: "Lato", sans-serif;
    position: relative;
  }
  .card {
    position: absolute;
    left: 280px;
    width: 640px;
    height: 372px;
    border-radius: 26px;
    overflow: hidden;
  }
  .card--front { top: 52px; }
  .card--back { top: 476px; background: var(--card-face); color: var(--ink); }

  .front-pattern {
    width: 100%;
    height: 100%;
    background: linear-gradient(135deg, var(--pattern-deep) 0%, var(--pattern-light) 45%, var(--pattern-deep) 100%);
  }

  .brand-badge {
    position: absolute;
    right: 46px;
    top: 26px;
    width: 150px;
    height: 150px;
    border-radius: 50%;
    background: var(--badge);
    display: flex;
    align-items: center;
    justify-content: center;
    text-align: center;
  }
  .brand-badge__name {
    font-weight: 700;
    font-size: 21px;
    line-height: 1.15;
    color: var(--badge-ink);
  }
  .rule-main {
    position: absolute;
    left: 46px;
    right: 46px;
    top: 196px;
    height: 1.5px;
    background: var(--rule);
  }
  .person { position: absolute; left: 46px; top: 214px; }
  .person__name { font-weight: 700; font-size: 28px; }
  .person__role { font-size: 17px; color: var(--ink-soft); margin-top: 6px; }
  .rule-short {
    position: absolute;
    left: 46px;
    top: 290px;
    width: 220px;
    height: 1.5px;
    background: var(--rule);
  }
  .contact-list {
    position: absolute;
    left: 46px;
    top: 298px;
    list-style: none;
  }
  .contact-list li {
    display: flex;
    align-items: center;
    gap: 12px;
    font-size: 19px;
    line-height: 23px;
  }
  .contact-list svg { width: 16px; height: 16px; fill: var(--ink); flex: none; }
  .address {
    position: absolute;
    right: 46px;
    top: 226px;
    text-align: right;
    font-size: 19px;
    line-height: 26px;
  }
</style>
</head>
<body>
  <section class="card card--front">
    <div class="front-pattern" role="img" aria-label="Embossed repeating brand pattern on black card stock"></div>
  </section>

  <section class="card card--back">
    <div class="brand-badge"><span class="brand-badge__name">Copper<br>Lantern</span></div>
    <div class="rule-main"></div>
    <div class="person">
      <p class="person__name">Daniel Hart</p>
      <p class="person__role">Owner</p>
    </div>
    <div class="rule-short"></div>
    <ul class="contact-list">
      <li>
        <svg viewBox="0 0 16 16" aria-hidden="true"><path d="M3.5 1 6 3.5 4.6 5.6c.9 2 2.6 3.7 4.6 4.6L11.3 8.8 14 11.3 12.6 14.2C6.8 14 2 9.2 1.8 3.4Z"/></svg>
        123.456.7890
      </li>
      <li>
        <svg viewBox="0 0 16 16" aria-hidden="true"><path d="M1 3h14v10H1Zm1.5 1.2L8 8.5l5.5-4.3Z"/></svg>
        info@webname.com
      </li>
      <li>
        <svg viewBox="0 0 16 16" aria-hidden="true"><path d="M8 1a7 7 0 1 0 0 14A7 7 0 0 0 8 1Zm0 1.5c.9 0 1.8 1.9 2 4.7H6c.2-2.8 1.1-4.7 2-4.7Zm-5.4 4.7a5.5 5.5 0 0 1 3-4.2c-.6 1.1-1 2.6-1.1 4.2Zm0 1.6h1.9c.1 1.6.5 3.1 1.1 4.2a5.5 5.5 0 0 1-3-4.2ZM8 13.5c-.9 0-1.8-1.9-2-4.7h4c-.2 2.8-1.1 4.7-2 4.7Zm2.4-.5c.6-1.1 1-2.6 1.1-4.2h1.9a5.5 5.5 0 0 1-3 4.2Zm1.1-5.8c-.1-1.6-.5-3.1-1.1-4.2a5.5 5.5 0 0 1 3 4.2Z"/></svg>
        www.website.com
      </li>
    </ul>
    <p class="address">421, Address line goes here<br>45452, Country name</p>
  </section>
</body>
</html>
```